Business Card for Professional Photographer

I'm looking for an eye catching modern clean design that compliments my logo/ website fonts & colours.
I specialise in architecture, corporate & commercial photography so I'm marketing to professional clients rather than portrait / wedding clients.

I would prefer to not have a solid black design.

My logo brand guide is as follows :

Main front font. : Reislust
Main font colour : #fff
Slogan front font : Ubuntu Bold
Monogram front font : Venti Medium
Container colour : #fff

I need print ready files in pdf .png & .eps formats.

Included in the files below are some screen grabs as reference to font & colours etc.

```html
<!DOCTYPE html>
<html lang="en">
<head>
<meta charset="utf-8">
<title>Northlight Frame — Business Card</title>
<link rel="stylesheet" href="https://fonts.googleapis.com/css2?family=Lato:wght@300;400;700&family=Ubuntu:wght@700&display=swap">
<style>
  :root {
    --canvas: #23262b;
    --paper: #ffffff;
    --gold-deep: #b8863f;
    --gold-mid: #d2a95c;
    --gold-light: #f3e9a0;
    --gold-text: #b8802e;
    --ink-grey: #6f6f6f;
    --white: #ffffff;
  }
  * { box-sizing: border-box; margin: 0; padding: 0; }
  html, body { width: 1200px; height: 900px; overflow: hidden; }
  body {
    background: var(--canvas);
    font-family: "Lato", Arial, sans-serif;
  }
  .stage {
    position: relative;
    width: 1200px;
    height: 900px;
  }
  .card {
    position: absolute;
    top: 285px;
    width: 540px;
    height: 330px;
    overflow: hidden;
    box-shadow: 0 10px 30px rgba(0,0,0,0.35);
  }
  .card--front { left: 40px; background: var(--paper); }
  .card--back  { left: 620px; }
  .card__art { position: absolute; inset: 0; width: 100%; height: 100%; }

  /* front side text */
  .front-content { position: absolute; left: 34px; top: 34px; }
  .brand-name {
    font-weight: 300;
    font-size: 22px;
    letter-spacing: 4px;
    color: var(--gold-text);
    line-height: 1;
  }
  .brand-tagline {
    font-family: "Ubuntu", Arial, sans-serif;
    font-weight: 700;
    font-size: 8px;
    letter-spacing: 2px;
    color: var(--gold-text);
    margin-top: 6px;
  }
  .divider {
    width: 12px; height: 3px;
    background: #4a4a4a;
    margin: 16px 0 18px;
  }
  .person-name {
    font-weight: 700;
    font-size: 18px;
    color: var(--gold-text);
    line-height: 1;
  }
  .person-role {
    font-weight: 300;
    font-size: 15px;
    color: var(--gold-text);
    margin-top: 2px;
  }
  .contact-list { list-style: none; margin-top: 12px; }
  .contact-list li {
    display: flex;
    align-items: center;
    gap: 8px;
    font-size: 14px;
    color: var(--ink-grey);
    line-height: 20px;
  }
  .contact-list svg { width: 12px; height: 12px; flex: none; }
  .location {
    font-size: 14px;
    color: var(--ink-grey);
    margin-top: 4px;
  }

  /* back side */
  .back-lockup {
    position: absolute;
    left: 0; right: 0; top: 96px;
    text-align: center;
    color: var(--white);
  }
  .back-mark {
    display: block;
    width: 54px; height: 54px;
    margin: 0 auto 18px;
    border: 3px solid var(--white);
    border-radius: 50%;
  }
  .back-name {
    font-weight: 300;
    font-size: 30px;
    letter-spacing: 6px;
    line-height: 1;
  }
  .back-tagline {
    font-family: "Ubuntu", Arial, sans-serif;
    font-weight: 700;
    font-size: 9px;
    letter-spacing: 2.6px;
    margin-top: 8px;
  }
</style>
</head>
<body>
<main class="stage">

  <!-- Front side -->
  <section class="card card--front">
    <svg class="card__art" viewBox="0 0 540 330" aria-hidden="true">
      <defs>
        <linearGradient id="frontGold" x1="0" y1="0" x2="1" y2="1">
          <stop offset="0" stop-color="#c08a3e"/>
          <stop offset="0.55" stop-color="#dcb970"/>
          <stop offset="1" stop-color="#f5ee9f"/>
        </linearGradient>
      </defs>
      <circle cx="520" cy="270" r="230" fill="url(#frontGold)"/>
      <path d="M330 250 C 335 150, 400 80, 490 62" fill="none" stroke="var(--paper)" stroke-width="5" stroke-linecap="round"/>
    </svg>

    <div class="front-content">
      <p class="brand-name">NORTHLIGHT FRAME</p>
      <p class="brand-tagline">Architecture Corporate Commercial</p>
      <div class="divider"></div>
      <p class="person-name">ADRIAN COLE</p>
      <p class="person-role">Photographer</p>
      <ul class="contact-list">
        <li>
          <svg viewBox="0 0 12 12"><circle cx="6" cy="6" r="5.2" fill="none" stroke="var(--gold-text)" stroke-width="1.2"/><path d="M4 3.6 L5 3.4 L5.6 4.8 L5 5.3 Q5.6 6.6 6.8 7 L7.3 6.4 L8.6 7 L8.4 8 Q6.6 8.6 5 7 Q3.4 5.4 4 3.6Z" fill="var(--gold-text)"/></svg>
          0400 555 017
        </li>
        <li>
          <svg viewBox="0 0 12 12"><rect x="0.8" y="2.2" width="10.4" height="7.6" fill="none" stroke="var(--gold-text)" stroke-width="1.2"/><path d="M1 2.6 L6 6.6 L11 2.6" fill="none" stroke="var(--gold-text)" stroke-width="1.2"/></svg>
          hello@northlightframe.com.au
        </li>
        <li>
          <svg viewBox="0 0 12 12"><circle cx="6" cy="6" r="5.4" fill="var(--gold-text)"/><path d="M0.8 6 H11.2 M6 0.6 V11.4" stroke="var(--paper)" stroke-width="0.8"/><ellipse cx="6" cy="6" rx="2.4" ry="5.4" fill="none" stroke="var(--paper)" stroke-width="0.8"/></svg>
          www.northlightframe.com.au
        </li>
      </ul>
      <p class="location">Greenvale Coast, Australia</p>
    </div>
  </section>

  <!-- Back side -->
  <section class="card card--back">
    <svg class="card__art" viewBox="0 0 540 330" aria-hidden="true">
      <defs>
        <radialGradient id="backGold" cx="0.5" cy="0.42" r="0.7">
          <stop offset="0" stop-color="#f6e8a6"/>
          <stop offset="0.35" stop-color="#dcbb72"/>
          <stop offset="1" stop-color="#b98640"/>
        </radialGradient>
      </defs>
      <rect width="540" height="330" fill="url(#backGold)"/>
      <circle cx="270" cy="140" r="250" fill="#ffffff" fill-opacity="0.06"/>
      <circle cx="270" cy="140" r="175" fill="#ffffff" fill-opacity="0.08"/>
    </svg>
    <div class="back-lockup">
      <span class="back-mark"></span>
      <p class="back-name">NORTHLIGHT FRAME</p>
      <p class="back-tagline">Architecture Corporate Commercial</p>
    </div>
  </section>

</main>
</body>
</html>
```